Company brochure for our unique consulting business

We are a small consulting business offering a unique set of services to our clients.. In simple terms we are a business improvement consultancy helping our clients get the best out of their businesses. We work with clients across multiple sectors and deliver a variety of services. We want to put together a brochure to cover these main themes:1. Who we are2. What we do3. The type of people we employ4. The sectors we work inWhile the brochure needs to have a certain corporate feel to it, we don't want it to be "boring" or "stiff". We would like it to have a slightly "friendly" or "informal" feel to it, to reflect the type of organisation we are.We have a company website http://brevalconsultingpartners.net , however we do not want to directly replicate the content or feel as we recognise it needs updating.We would like the brochure to be A4 portrait format. We anticipate requiring 12 sides (including covers) but we are happy to be guided on this based on the content we have provided.The attached ppt file gives the detail of the content to be included and also shows the proposed pagination. For the front cover we would like to try 2 versions, one with the BCP logo and one with the Breval Consulting Partners logo (a file of both is attached)One of the most important pages will be the "Our Services" page. We would like this to cover the centre fold. In the ppt file we have shown an example layout, but this is where we need most help - we are clearly not graphic designers! This page will be the most used page in sales meetings etc.Also attached is the following:1. file for our BrevalConsulting Partners company logo.2. File for our BCP company logo3. Files for Derek's signatures (for under photos) - Owen's to follow4. Photo of Derek & Owen (person in purple shirt to be cropped out)Thank you and really excited to see what everyone comes back with.Derek & Owen

Target Market(s)

Very broad - Manufacturing, Healthcare, Hospitality

Industry/Entity Type

Management Consulting

Font styles to use
Other font styles liked:
• We use Swiss721, but happy to be guided by designer

Colors
3276b5
85abd2
0355a3
333333
5c5c5c
9d9d9d
d9d9d9

Requirements
Must have
• Corporate feel
Nice to have
• Slightly friendly feel
• Our standard "blue" is (CORRECTION) - R55 G96 B146 #376092 and our standard grey is R197 G178, B179 - #B3B2B2, which we would like to keep, but other colours we are happy to be guided on. Brand guidelines attached.

```html
<!DOCTYPE html>
<html lang="en">
<head>
<meta charset="utf-8">
<title>Breval Consulting Partners – Brochure Covers</title>
<link href="https://fonts.googleapis.com/css2?family=Montserrat:wght@400;700;800&display=swap" rel="stylesheet">
<style>
  :root {
    --page-bg: #666666;
    --paper: #ffffff;
    --navy: #233f8b;
    --sky: #c3d5ea;
    --ink-blue: #25408f;
    --soft-blue: #7c9fd0;
    --icon-blue: #6f96c9;
    --logo-ink: #111111;
    --photo-light: #e6e6e6;
    --photo-dark: #9a9a9a;
  }
  * { margin: 0; padding: 0; box-sizing: border-box; }
  html, body {
    width: 1200px; height: 1200px; overflow: hidden;
    background: var(--page-bg);
    font-family: "Montserrat", sans-serif;
  }
  .spread {
    position: absolute; left: 0; top: 175px;
    width: 1338px; height: 948px;
    background: var(--paper);
    transform: scale(0.8969);
    transform-origin: top left;
    overflow: hidden;
  }
  .spread-shapes { position: absolute; inset: 0; }
  .brand-name {
    position: absolute; left: 771px; top: 98px;
    font-weight: 700; font-size: 38px; line-height: 1.05;
    color: var(--logo-ink); letter-spacing: -0.5px;
  }
  .contact-title {
    position: absolute; left: 64px; top: 730px;
    font-size: 20px; font-weight: 700; color: var(--ink-blue);
  }
  .contact-list {
    position: absolute; left: 62px; top: 784px;
    list-style: none; color: var(--ink-blue); font-size: 14px; line-height: 16px;
  }
  .contact-list li { display: flex; gap: 10px; align-items: flex-start; margin-bottom: 3px; }
  .contact-list svg { width: 18px; height: 16px; flex: none; fill: var(--icon-blue); }
  .web-address {
    position: absolute; left: 420px; top: 864px;
    font-size: 9px; font-weight: 700; color: var(--ink-blue);
  }
  .cover-title {
    position: absolute; left: 776px; top: 768px;
    font-size: 47px; font-weight: 800; color: var(--ink-blue);
  }
  .cover-intro {
    position: absolute; left: 777px; top: 838px; width: 520px;
    font-size: 13.5px; line-height: 16px; color: var(--soft-blue);
  }
</style>
</head>
<body>
  <div class="spread">
    <svg class="spread-shapes" viewBox="0 0 1338 948" width="1338" height="948">
      <defs>
        <linearGradient id="photoTone" x1="0" y1="0" x2="1" y2="1">
          <stop offset="0" stop-color="var(--photo-light)"/>
          <stop offset="1" stop-color="var(--photo-dark)"/>
        </linearGradient>
      </defs>
      <line x1="1011" y1="157" x2="1338" y2="157" stroke="var(--sky)" stroke-width="3"/>
      <polygon points="346,230 1338,230 1338,370 1261,740 243,740" fill="var(--sky)"/>
      <rect x="0" y="246" width="669" height="443" fill="var(--navy)"/>
      <polygon points="669,246 1218,246 1128,689 669,689" fill="url(#photoTone)"
               role="img" aria-label="Black and white photo of the two founders seated at a meeting table"/>
    </svg>

    <div class="brand-name">Breval<br>Consulting</div>

    <h2 class="contact-title">Contact Us</h2>
    <ul class="contact-list">
      <li>
        <svg viewBox="0 0 18 16" aria-hidden="true"><path d="M9 0a5.5 5.5 0 0 0-5.5 5.5C3.5 9.5 9 16 9 16s5.5-6.5 5.5-10.5A5.5 5.5 0 0 0 9 0zm0 7.5a2 2 0 1 1 0-4 2 2 0 0 1 0 4z"/></svg>
        <span>BCP Limited<br>Millbrook House<br>Canal Lane, Leicester, LE1 4QT</span>
      </li>
      <li>
        <svg viewBox="0 0 18 16" aria-hidden="true"><circle cx="9" cy="8" r="8"/><path d="M6 4.5l1.6-.4 1 2.2-1 .8a6 6 0 0 0 2.6 2.6l.8-1 2.2 1-.4 1.6c-3.5.3-7-3.2-6.8-6.8z" fill="#fff"/></svg>
        <span>+44 (0) 1632 960418</span>
      </li>
      <li>
        <svg viewBox="0 0 18 16" aria-hidden="true"><path d="M0 3h18v10H0z"/><path d="M0 3l9 6 9-6M0 13l6-5M18 13l-6-5" stroke="#fff" stroke-width="1.2" fill="none"/></svg>
        <span>enquiries@brevalgroup.net</span>
      </li>
    </ul>
    <p class="web-address">www.brevalgroup.net</p>

    <h1 class="cover-title">Text Here</h1>
    <p class="cover-intro">At BCP we constantly strive to deliver the best possible value for our clients. Importantly we recognize, it's our clients that define value, not us.</p>
  </div>
</body>
</html>
```